Local Chiropractoc needs Modern Website

This website needs to have an upscale look with a very modern feel.

This is for a home page psd layout and an interior page psd file so 2 files total

Below is the information and websites to reference

Add Logo that is attached.

Build a color scheme similar to this website image titled "chiro-1" using the golds, whites, blacks and browns from the color of the logo

I want to see a light background so it makes the images and logo stick out

Must Include these pages in a horizontal menu bar in this order:
Home, Why Fair Ridge?, How Chiropractic Helps, Ask the Doctor, Work Place Wellness, Request an Appointment, Blog, Contact Us

Please add the following social media logos to the top and footer of the website: Chatterly, Plexo+, Vidzio

Build a "classy looking" Make An Appointment Button into the header with the contact info below

Phone Number:
555-014-2297

Address:
4172 North Maple Blvd, Suite #7
Millbrook, FL 34209

This website needs 4 rotating banners. Please reference a layout similar to this for the banners: http://hollowpinespine.com/. However design it nicer than this website

Below are the description for each banner

Rotating Banner #1
Use Image: Patients are Saying
Add a line of text: "What our Patients are Saying"

Rotating Banner #2
Use Image: Becoming a Patient
Add a line of text: "Interested in Becoming a Patient"

Rotating Banner #3
Use Image: Dinner with Doctor
Add a line of text: "Win A free Dinner with Dr. Hollins"

Rotating Banner #4
Use Image: Chatterly
Add a line of text: Follow us on Chatterly
Bullet point these 4 lines underneath the "Follow us on Chatterly" text:
- Cutting Edge Health News
- Healthy Recipes
- Newest Health Products
- Clinic Events

I'd like to see a free consultation box similar to the "chiro-1" image. Fields to include are: First Name, Last Name, Phone Number, Comments

For the body, please fill it with latin text. Please design a professional 2 column layout similar to the www.hollowpinespine.com website. (DO NOT COPY THIS WEBSITE, USE IT AS REFERENCE)

In the left column include in this order:
Video
Rate us on Plexo Button, Find us on Chatterly Button
Welcome Letter

In the right column include this:

Office Hours
Monday: 8:00-11:00, 2:00-5:00
Tuesday: 8:30-11:00, 2:00-5:30
Wednesday: 8:00-11:00, 2:00-5:00
Thursday: 10:00-12:00, 2:30-5:00
Friday: 8:00-10:00, 1:00-5:00
Saturday: Closed
Sunday: Closed

Patient Testimonials
Fill with a latin text testimonial. This spot will rotate different testimonials

For the footer please design something similar to the layout of this: http://www.tidewellhealer.com/

Also include in the Footer: Powered by Crestline Pixel Group

```html
<!DOCTYPE html>
<html lang="en">
<head>
<meta charset="utf-8">
<title>Fair Ridge Chiropractic</title>
<link href="https://fonts.googleapis.com/css2?family=Open+Sans:ital,wght@0,400;0,600;0,700;0,800;1,400;1,600&display=swap" rel="stylesheet">
<style>
:root{
  --gold:#b39553;
  --gold-dark:#9c7f42;
  --ink:#2b2b2b;
  --ink-soft:#3a3a3a;
  --page:#f2f2f2;
  --paper:#ffffff;
  --text:#777777;
  --line:#e6e6e6;
}
*{margin:0;padding:0;box-sizing:border-box}
html,body{width:805px;height:1200px;overflow:hidden}
body{background:var(--page);font-family:"Open Sans",Arial,sans-serif;position:relative;color:var(--text)}
.abs{position:absolute}

/* header */
.brand{left:108px;top:52px;display:flex;align-items:center;gap:8px}
.brand-mark{width:14px;height:40px;background:var(--ink)}
.brand-name{font-weight:800;font-size:24px;color:var(--ink);letter-spacing:-.5px;line-height:1.05}
.top-social{right:102px;top:51px;display:flex;gap:4px}
.circle{width:17px;height:17px;border-radius:50%;border:1px solid var(--gold);color:var(--gold);font-size:6px;font-weight:700;display:flex;align-items:center;justify-content:center}
.circle.on{background:var(--gold);color:#fff}
.contact-bar{left:347px;top:79px;width:256px;height:29px;background:var(--ink);border-radius:3px 0 0 3px;display:flex;align-items:center}
.contact-item{display:flex;align-items:center;gap:7px;padding:0 9px;height:100%;white-space:nowrap}
.contact-item + .contact-item{border-left:1px solid #444}
.contact-item strong{display:block;color:#fff;font-size:6.5px;font-weight:700}
.contact-item em{display:block;color:#8a8a8a;font-size:6px}
.appt-btn{left:596px;top:79px;width:115px;height:29px;background:var(--gold);clip-path:polygon(8px 0,100% 0,100% 100%,0 100%);color:#fff;font-size:6.8px;font-weight:700;display:flex;align-items:center;justify-content:center;letter-spacing:.2px}

/* nav */
.main-nav{left:93px;top:121px;width:618px;height:40px;background:var(--ink);display:flex;border-radius:2px}
.main-nav a{color:#fff;font-size:6.4px;text-decoration:none;display:flex;align-items:center;justify-content:center;border-right:1px solid #3f3f3f;text-transform:uppercase;white-space:nowrap}
.main-nav a:last-child{border-right:0}
.main-nav a.active{background:var(--gold)}

/* banner */
.banner{left:93px;top:171px;width:618px;height:202px;overflow:hidden;border-radius:2px}
.banner-photo{position:absolute;left:0;top:0;width:440px;height:202px;background:linear-gradient(135deg,#f3efe6 0%,#eadcc6 45%,#e9a84a 75%,#8aa346 100%)}
.banner-panel{position:absolute;left:0;top:0}
.banner-copy{position:absolute;left:453px;top:37px;color:#fff}
.banner-copy h2{font-size:14px;font-weight:700;line-height:1.3}
.banner-copy ul{list-style:none;margin-top:8px}
.banner-copy li{font-size:6.5px;font-style:italic;line-height:15px}
.dots{display:flex;gap:3px}
.dots span{width:5px;height:5px;border-radius:50%;background:rgba(255,255,255,.35)}
.dots span.on{background:#fff}
.banner .dots{position:absolute;left:452px;top:186px}

/* content */
.content{left:93px;top:382px;width:618px;height:717px;background:var(--paper);border-radius:3px 3px 0 0}
.section-title{display:flex;align-items:center;gap:6px;font-size:8px;font-weight:700;color:var(--ink);text-transform:uppercase;white-space:nowrap}
.section-title::before{content:"";width:2px;height:8px;background:var(--gold)}
.section-title::after{content:"";flex:1;height:5px;background:#f3f3f3}
.video-frame{left:108px;top:435px;width:387px;height:200px;border:1px solid var(--line);padding:5px}
.video-still{width:100%;height:170px;background:linear-gradient(160deg,#c9c9c3 0%,#b7b29d 40%,#8a9b63 100%);position:relative}
.play{position:absolute;left:50%;top:50%;width:24px;height:22px;margin:-11px 0 0 -12px;background:rgba(255,255,255,.55);border-radius:2px}
.video-controls{height:20px;background:var(--ink);display:flex;align-items:center;gap:6px;padding:0 6px;font-size:5.5px;color:#888}
.track{flex:1;height:2px;background:#555;position:relative}
.track i{position:absolute;left:0;top:0;width:28%;height:2px;background:var(--gold)}
.track b{position:absolute;left:28%;top:-2px;width:6px;height:6px;border-radius:50%;background:#fff}
.letter{left:108px;top:675px;width:387px;font-size:6.7px;line-height:15px}
.letter p{margin-bottom:15px}
.letter-photo{float:right;width:186px;height:164px;margin:2px 0 6px 10px;background:linear-gradient(150deg,#c5d8a8 0%,#e4b8a3 50%,#9bbd7c 100%)}

/* right column */
.consult{left:510px;top:413px;width:187px;height:230px}
.consult-head{position:absolute;left:0;top:12px;width:187px;text-align:center;color:#fff}
.consult-head small{display:block;font-size:6.8px}
.consult-head strong{display:block;font-size:11px;font-weight:700;margin-top:1px}
.consult-form{position:absolute;left:10px;top:60px;width:167px}
.consult-form h4{color:#fff;font-size:7px;font-style:italic;font-weight:700;text-align:center;margin-bottom:6px}
.field{background:#fff;border-radius:2px;height:17px;margin-bottom:4px;font-size:5.8px;color:#555;padding:5px 10px}
.field.gold{color:var(--gold)}
.field.tall{height:40px}
.submit{display:inline-block;background:var(--gold);color:#fff;font-size:6px;font-weight:700;padding:5px 10px;border:1px solid #d3bd87;border-radius:2px;margin-top:1px}
.rate-btn{left:510px;width:187px;height:30px;background:var(--ink);display:flex;border-radius:2px}
.rate-btn .ico{width:31px;background:var(--ink-soft);color:#fff;font-size:9px;font-weight:700;display:flex;align-items:center;justify-content:center}
.rate-btn .lbl{flex:1;text-align:center;color:var(--gold);padding-top:4px}
.rate-btn .lbl small{display:block;color:#fff;font-size:5.6px;font-weight:600}
.rate-btn .lbl strong{display:block;font-size:13px;font-weight:800;line-height:1.05}
.hours{left:510px;top:739px;width:187px;border:1px solid var(--line)}
.hours h3{background:var(--gold);color:#fff;font-size:8px;font-weight:700;text-align:center;height:24px;line-height:24px}
.hours table{width:100%;border-collapse:collapse;font-size:5.6px}
.hours td{height:18px;padding:0 9px;border-top:1px solid #fff;white-space:nowrap}
.hours tr:nth-child(odd) td{background:#f4f4f4}
.hours td:first-child{font-weight:700;color:#444}
.hours td:last-child{text-align:right;color:#999}
.hours tr.closed td{color:var(--gold)}
.testimonial{left:510px;top:932px;width:187px;height:138px;background:#f0f0f0;border:1px solid var(--line)}
.testimonial blockquote{position:absolute;left:14px;top:12px;width:162px;font-size:6.3px;font-style:italic;line-height:13px;color:#999;text-indent:28px}
.quote-mark{position:absolute;left:16px;top:8px;font-size:34px;font-weight:800;color:var(--gold);line-height:1}
.testimonial footer{position:absolute;left:0;bottom:0;width:100%;height:21px;background:var(--gold);display:flex;align-items:center;justify-content:space-between;padding:0 15px;color:#fff;font-size:6px;font-weight:700}
.testimonial .dots span{background:rgba(255,255,255,.5)}
.testimonial .dots span.on{background:#fff}

/* footer */
.foot-top{left:0;top:1099px;width:805px;height:51px;background:var(--gold)}
.foot-links{position:absolute;left:108px;top:20px;font-size:6.7px;color:#fff;font-weight:600;white-space:nowrap}
.foot-links span{margin:0 4px}
.foot-brand{position:absolute;left:637px;top:16px;display:flex;align-items:center;gap:5px}
.foot-brand i{width:6px;height:20px;background:#fff}
.foot-brand b{color:#fff;font-size:12px;font-weight:800;white-space:nowrap}
.foot-bottom{left:0;top:1150px;width:805px;height:50px;background:var(--ink)}
.foot-address{position:absolute;left:108px;top:15px;color:#fff;font-size:6.5px;font-weight:700;line-height:9px;white-space:nowrap}
.foot-address em{font-weight:400;display:block;padding-left:25px}
.foot-social{position:absolute;left:367px;top:14px;display:flex;gap:6px}
.sq{width:20px;height:20px;border:1px solid var(--gold);color:var(--gold);border-radius:2px;font-size:6px;font-weight:700;display:flex;align-items:center;justify-content:center}
.sq.on{background:var(--gold);color:#fff}
.foot-copy{position:absolute;right:108px;top:15px;color:#fff;font-size:6.5px;font-weight:700;line-height:9px;text-align:right;white-space:nowrap}
.foot-copy em{font-weight:400;display:block;padding-right:20px}
.foot-copy em span{color:var(--gold)}
</style>
</head>
<body>

<header>
  <div class="abs brand"><span class="brand-mark"></span><span class="brand-name">FAIR RIDGE<br>CHIROPRACTIC</span></div>
  <div class="abs top-social"><span class="circle">C</span><span class="circle on">P+</span><span class="circle">V</span></div>
  <div class="abs contact-bar">
    <div class="contact-item">
      <svg width="12" height="12" viewBox="0 0 24 24"><path fill="#b39553" d="M6.6 10.8a15.1 15.1 0 0 0 6.6 6.6l2.2-2.2c.3-.3.7-.4 1-.2 1.1.4 2.3.6 3.6.6.6 0 1 .4 1 1V20c0 .6-.4 1-1 1A17 17 0 0 1 3 4c0-.6.4-1 1-1h3.5c.6 0 1 .4 1 1 0 1.3.2 2.5.6 3.6.1.3 0 .7-.2 1z"/></svg>
      <div><strong>555-014-2297</strong><em>info@example.com</em></div>
    </div>
    <div class="contact-item">
      <svg width="13" height="12" viewBox="0 0 24 22"><path fill="#b39553" d="M12 1 1 11h3v10h6v-6h4v6h6V11h3z"/></svg>
      <div><strong>4172 North Maple Blvd, Suite #7</strong><em>Millbrook, FL 34209</em></div>
    </div>
  </div>
  <a class="abs appt-btn">MAKE AN APPOINTMENT</a>

  <nav class="abs main-nav">
    <a style="width:50px">Home</a>
    <a class="active" style="width:71px">Why Fair Ridge?</a>
    <a style="width:107px">How Chiropractic Helps</a>
    <a style="width:76px">Ask the Doctor</a>
    <a style="width:99px">Work Place Wellness</a>
    <a style="width:108px">Request an Appointment</a>
    <a style="width:38px">Blog</a>
    <a style="width:69px">Contact Us</a>
  </nav>
</header>

<section class="abs banner">
  <div class="banner-photo" role="img" aria-label="Photo of a cheerful baby flexing beside orange juice and fresh fruit"></div>
  <svg class="banner-panel" width="618" height="202" viewBox="0 0 618 202">
    <path d="M412 0H618V202H415C430 170 405 150 392 120C380 90 398 60 400 35C401 18 398 6 412 0Z" fill="#b39553"/>
  </svg>
  <div class="banner-copy">
    <h2>Follow Us on<br>Chatterly</h2>
    <ul>
      <li>- Cutting Edge Health News</li>
      <li>- Healthy Recipes</li>
      <li>- Newest Health Products</li>
      <li>- Clinic Events</li>
    </ul>
  </div>
  <div class="dots"><span></span><span class="on"></span><span></span><span></span></div>
</section>

<main class="abs content"></main>

<h3 class="abs section-title" style="left:108px;top:412px;width:387px">Our Videos</h3>
<div class="abs video-frame">
  <div class="video-still" role="img" aria-label="Video still of a smiling family of three generations outdoors"><span class="play"></span></div>
  <div class="video-controls">
    <svg width="6" height="7" viewBox="0 0 6 7"><path d="M0 0 6 3.5 0 7z" fill="#888"/></svg>
    <span>00:28</span><div class="track"><i></i><b></b></div><span>02:36</span>
  </div>
</div>

<h3 class="abs section-title" style="left:108px;top:655px;width:387px">Welcome Letter</h3>
<article class="abs letter">
  <div class="letter-photo" role="img" aria-label="Photo of a happy family of four embracing outdoors"></div>
  <p>Hello Dear Visitor,<br>Vestibulum malesuada tortor volutpat risus finibus, in con sequat nibh dictum. Pellen tesque vestibulum nisi nisl, vel accumsan dui consequat sed. Integer non justo et mi interd um pretium. Proin ut pulvinar eros. Pellentesque at luctus odio, a ullamcorper urna. Nam semper feugiat massa non pulvinar. Curabitur sagittis, odio eget posuere ultricies, sem nisi pulvinar turpis, at laoreet arcu neque lacinia odio. Nulla nec nunc ac felis auctor fermentum quis ut justo. Donec ultricies feugiat accumsan. Integer leo justo, dapi bus id mauris quis, vestibulum rutrum arcu.</p>
  <p style="clear:both">Vestibulum malesuada tortor volutpat risus finibus, in con sequat nibh dictum. Pellen tesque vestibulum nisi nisl, vel accumsan dui consequat sed. Integer non justo et mi interd um pretium. Proin ut pulvinar eros. Pellentesque at luctus odio, a ullamcorper urna. Nam semper feugiat massa non pulvinar. Curabitur sagittis, odio eget posuere ultricies, sem nisi pulvinar turpis, at laoreet arcu neque lacinia odio. Nulla nec nunc ac felis auctor fermentum quis ut justo. Donec ultricies feugiat accumsan. Integer leo justo, dapi bus id mauris quis, vestibulum rutrum arcu. Donec diam magna, mattis ac odio id, dignis sim euismod eros. Proin id luctus dolor, vel imperdiet ante. Morbi rhoncus fringilla neque, non tristique ante interdum ac. Etiam lacinia neque sagittis, commodo diam at, ullamcorper urna.</p>
  <p>In sodales velit nec magna pellentesque, nec dignissim eros porta. Nam congue maximus elit. Quisque sapien nunc, lobortis et nulla eu, eleifend sodales velit. Aliquam aliquam eros lectus, facilisis dictum libero feugiat nec. Nunc quis elit pulvinar, aliquam ipsum in, lacinia enim. Fusce a consequat erat. Aliquam urna dui, malesuada in vehicula cursus, porttitor quis risus. Pellentesque tristique consectetur libero, et suscipit eros fringilla et. Morbi fringilla sapien sed elit lobortis, non cursus velit tincidunt.</p>
</article>

<aside>
  <div class="abs consult">
    <svg width="187" height="230" viewBox="0 0 187 230" style="position:absolute;left:0;top:0">
      <path d="M0 0H187V208L93.5 230 0 208Z" fill="#2b2b2b"/>
      <path d="M0 0H187V33L93.5 54 0 33Z" fill="#b39553"/>
    </svg>
    <div class="consult-head"><small>CONTACT US NOW &amp; GET YOUR</small><strong>FREE CONSULTATION</strong></div>
    <form class="consult-form">
      <h4>WELLNESS BEGINS HERE</h4>
      <div class="field">First Name</div>
      <div class="field gold">Last Name</div>
      <div class="field">Phone Number</div>
      <div class="field tall">Comments ...</div>
      <span class="submit">Submit ➜</span>
    </form>
  </div>

  <a class="abs rate-btn" style="top:653px"><span class="ico">P+</span><span class="lbl"><small>RATE US ON</small><strong>PLEXO</strong></span></a>
  <a class="abs rate-btn" style="top:688px"><span class="ico">C</span><span class="lbl"><small>FIND US ON</small><strong>CHATTERLY</strong></span></a>

  <div class="abs hours">
    <h3>OFFICE HOURS</h3>
    <table>
      <tr><td>Monday</td><td>8:00-11:00 AM, 2:00-5:00 PM</td></tr>
      <tr><td>Tuesday</td><td>8:30-11:00 AM, 2:00-5:30 PM</td></tr>
      <tr><td>Wednesday</td><td>8:00-11:00 AM, 2:00-5:00 PM</td></tr>
      <tr><td>Thursday</td><td>10:00-12:00 AM, 2:30-5:00 PM</td></tr>
      <tr><td>Friday</td><td>8:00-10:00 AM, 1:00-5:00 PM</td></tr>
      <tr class="closed"><td>Saturday</td><td>Closed</td></tr>
      <tr class="closed"><td>Sunday</td><td>Closed</td></tr>
    </table>
  </div>

  <h3 class="abs section-title" style="left:510px;top:909px;width:187px">Patient Testimonials</h3>
  <div class="abs testimonial">
    <span class="quote-mark">“</span>
    <blockquote>Pellentesque habitant morbi tristique senectus et netus et malesuada fames ac turpis egestas. Donec faucibus aliquet dui, nec congue orci sagittis eget. Integer leo justo, dapibus id mauris quis, vestibulum rutrum arcu. Etiam sed ipsum eu augue condimentum ullam corper vel ac sapien.</blockquote>
    <footer><span>- Mr. Dale Brenner -</span><span class="dots"><span></span><span class="on"></span><span></span><span></span></span></footer>
  </div>
</aside>

<footer>
  <div class="abs foot-top">
    <div class="foot-links">Home<span>|</span>Why Fair Ridge?<span>|</span>How Chiropractic Helps<span>|</span>Ask the Doctor<span>|</span>Work Place Wellness<span>|</span>Request an Appointment<span>|</span>Blog<span>|</span>Contact Us</div>
    <div class="foot-brand"><i></i><b>FAIR RIDGE</b></div>
  </div>
  <div class="abs foot-bottom">
    <div class="foot-address">4172 North Maple Blvd, Suite #7<em>Millbrook, FL 34209</em></div>
    <div class="foot-social"><span class="sq">C</span><span class="sq on">P+</span><span class="sq">V</span></div>
    <div class="foot-copy">Copyright © 2015, Fair Ridge Chiropractic<em>Powered by <span>Crestline Pixel Group</span></em></div>
  </div>
</footer>

</body>
</html>
```